Business Card Design needed for start up company Halvora

In need of a new business card designed for a start up company based in Sydney, Halvora is a new start up innovative Company, our mission it to make property accessible for everyday Australian and to become the leading Real Estate platform in Australia. We want it to be fresh and clean.

Industry/Entity Type

Financial

Contact Information for Business Card

Section for Name
Section for Title

HALVORA - The Strength of Pooling
Mobile:
Direct:

Font styles to use
Sans Serif

Colors
33a6d7
0692cd
0255a3
ffffff

Requirements
Must have
• Logo, all business card details

```html
<!DOCTYPE html>
<html lang="en">
<head>
<meta charset="utf-8">
<title>Halvora Business Card</title>
<link rel="stylesheet" href="https://fonts.googleapis.com/css2?family=Exo+2:wght@400;500;700&display=swap">
<style>
  :root {
    --sky: #4dbaea;
    --sky-accent: #33a6d7;
    --ink: #3a3a3c;
    --paper: #ffffff;
    --backdrop: #e9ecef;
  }
  * { box-sizing: border-box; margin: 0; padding: 0; }
  html, body {
    width: 1200px;
    height: 1000px;
    overflow: hidden;
    background: var(--backdrop);
    font-family: "Exo 2", sans-serif;
  }
  .card {
    position: absolute;
    left: 250px;
    width: 700px;
    height: 400px;
    border-radius: 22px;
    box-shadow: 0 6px 18px rgba(0, 0, 0, 0.12);
  }
  .card--front {
    top: 60px;
    background: var(--sky);
    display: flex;
    align-items: center;
    justify-content: center;
  }
  .card--back {
    top: 520px;
    background: var(--paper);
  }
  .brand-name {
    font-weight: 700;
    letter-spacing: 4px;
    line-height: 1;
  }
  .brand-name--large { color: var(--paper); font-size: 60px; }
  .brand-name--small {
    position: absolute;
    top: 52px;
    right: 50px;
    color: var(--ink);
    font-size: 30px;
    letter-spacing: 3px;
  }
  .person {
    position: absolute;
    left: 58px;
    top: 128px;
  }
  .person__name {
    font-size: 34px;
    font-weight: 700;
    color: var(--ink);
    letter-spacing: 1.5px;
    line-height: 1;
  }
  .person__title {
    font-size: 22px;
    font-weight: 400;
    color: var(--sky-accent);
    letter-spacing: 1px;
    margin-top: 4px;
  }
  .divider {
    position: absolute;
    left: 50px;
    right: 50px;
    top: 212px;
    height: 2px;
    background: var(--sky-accent);
  }
  .contact {
    position: absolute;
    left: 50px;
    top: 236px;
    list-style: none;
  }
  .contact__item {
    display: flex;
    align-items: center;
    gap: 14px;
    font-size: 19px;
    color: var(--ink);
    letter-spacing: 0.5px;
    height: 28px;
  }
  .contact__icon { width: 16px; height: 16px; fill: var(--sky-accent); flex: none; }
  .contact__highlight { color: var(--sky-accent); }
  .address {
    position: absolute;
    right: 50px;
    bottom: 34px;
    text-align: right;
    font-size: 19px;
    font-style: normal;
    color: var(--ink);
    letter-spacing: 0.5px;
    line-height: 1.35;
  }
  .address__icon {
    display: block;
    margin: 0 0 6px auto;
    width: 22px;
    height: 18px;
  }
</style>
</head>
<body>
  <section class="card card--front">
    <span class="brand-name brand-name--large">HALVORA</span>
  </section>

  <section class="card card--back">
    <span class="brand-name brand-name--small">HALVORA</span>

    <div class="person">
      <h1 class="person__name">ELENA MARSH</h1>
      <p class="person__title">Director</p>
    </div>

    <div class="divider"></div>

    <ul class="contact">
      <li class="contact__item">
        <svg class="contact__icon" viewBox="0 0 16 16"><path d="M3.2 1.5l2.3 0.2 1.1 3-1.5 1.2c0.8 1.8 2.2 3.2 4 4l1.2-1.5 3 1.1 0.2 2.3c-0.4 1.2-1.6 2-2.9 1.8C5.8 13 3 10.2 1.4 5.4 1.2 4.1 2 2.9 3.2 1.5z"/></svg>
        <span>000 123 456 789</span>
      </li>
      <li class="contact__item">
        <svg class="contact__icon" viewBox="0 0 16 16"><path d="M4.5 0.5h7a1 1 0 0 1 1 1v13a1 1 0 0 1-1 1h-7a1 1 0 0 1-1-1v-13a1 1 0 0 1 1-1zM5 2.5v9.5h6V2.5zM8 12.8a0.9 0.9 0 1 0 0 1.8 0.9 0.9 0 0 0 0-1.8z"/></svg>
        <span>000 222 3334</span>
      </li>
      <li class="contact__item">
        <svg class="contact__icon" viewBox="0 0 16 16"><path d="M1 3h14v10H1zM2.5 4.5v0.3L8 9l5.5-4.2v-0.3zM2.5 6.6v4.9h11V6.6L8 10.8z"/></svg>
        <span>urname@email.com</span>
      </li>
      <li class="contact__item">
        <svg class="contact__icon" viewBox="0 0 16 16"><path d="M8 1a7 7 0 1 0 0 14A7 7 0 0 0 8 1zm0 1.3c0.9 0.8 1.6 2.3 1.8 4H6.2C6.4 4.6 7.1 3.1 8 2.3zM5 6.3H2.4A5.7 5.7 0 0 1 6 2.6 7.6 7.6 0 0 0 5 6.3zm-2.6 1.4H5a7.6 7.6 0 0 0 1 3.7 5.7 5.7 0 0 1-3.6-3.7zm3.8 0h3.6c-0.2 1.7-0.9 3.2-1.8 4-0.9-0.8-1.6-2.3-1.8-4zm4.8 0h2.6A5.7 5.7 0 0 1 10 11.4a7.6 7.6 0 0 0 1-3.7zm0-1.4a7.6 7.6 0 0 0-1-3.7 5.7 5.7 0 0 1 3.6 3.7z"/></svg>
        <span>www.<span class="contact__highlight">websitename</span>.com</span>
      </li>
    </ul>

    <address class="address">
      <svg class="address__icon" viewBox="0 0 22 18"><path d="M11 1L21 17 11 12 1 17z" fill="none" stroke="#33a6d7" stroke-width="1.4" stroke-linejoin="round"/></svg>
      Your Street Address,<br>
      Singapore, 1234
    </address>
  </section>
</body>
</html>
```